Bright Harbor website redesign

We need a redesign for a website: mybrightharbor.example.

I already created a video going over what exactly is needed in the design.

See Video here: https://files.example.net/file/d/7xQpL2mR9vTz4KwB8nYcH3jDs6FgA1eU0/view?usp=sharing

Searchly Slide shown in Video: https://slides.example.net/presentation/d/9KP_Rtnwq3XbzmLeYc7VhJ2GoUd4Fs_PaiTe6q1kQ5Wr/edit?usp=sharing

Holidays in India so we did not get enough design entries or quality.

Target Market(s)

Dentistry

Industry/Entity Type

Dentistry

Number of Pages Required

1 page

Colors
0094D4
00A9DD
6FCCEA
C7EBF8
E9F6FB
00AB8E
00BBA5
67D7C9
C6EFE9
E9F9F6

Requirements
Must have
• See 13 min video link in description - shows what to do.

```html
<!DOCTYPE html>
<html lang="en">
<head>
<meta charset="utf-8">
<title>Bright Harbor – Dental Care</title>
<link href="https://fonts.googleapis.com/css2?family=Montserrat:wght@400;500;600&family=Raleway:wght@400;500;700;800&display=swap" rel="stylesheet">
<style>
:root{
  --brand-green:#6aa84f;
  --accent-red:#e0262c;
  --blue:#1492d1;
  --blue-dark:#0b74ad;
  --blue-light:#2aa9de;
  --team-dark:#1c3320;
  --team-mid:#2e5532;
  --testi-green:#5e9156;
  --ink:#222;
  --muted:#555;
  --line:#e2e2e2;
  --soft-bg:#f4f8fb;
  --footer-bg:#232323;
  --footer-bar:#1a1a1a;
  --footer-head:#7cb24f;
  --star:#f5b800;
}
*{margin:0;padding:0;box-sizing:border-box}
html,body{width:1200px;height:3992px;overflow:hidden}
body{position:relative;font-family:"Montserrat",sans-serif;color:var(--ink);background:#fff}
.abs{position:absolute}
.section{position:absolute;left:0;width:1200px;overflow:hidden}

/* header */
.site-header{top:0;height:84px;background:#fff;border-bottom:4px solid var(--brand-green)}
.brand{left:130px;top:26px;font-family:"Raleway",sans-serif;font-weight:700;font-size:27px;color:var(--brand-green);display:flex;align-items:center;gap:10px}
.brand-dot{width:14px;height:14px;border-radius:50%;background:var(--accent-red)}
.topline{left:694px;top:14px;font-size:11px;color:#333}
.topline b{color:var(--accent-red);font-weight:600}
.btn-pill{top:6px;height:32px;border-radius:16px;color:#fff;font-size:10.5px;font-weight:600;display:flex;align-items:center;justify-content:center;letter-spacing:.2px}
.btn-schedule{left:826px;width:128px;background:var(--blue)}
.btn-emergency{left:961px;width:109px;background:var(--accent-red)}
.nav a{position:absolute;top:51px;transform:translateX(-50%);font-size:11px;color:#333;text-decoration:none;white-space:nowrap}
.nav a.active{color:var(--brand-green)}
.nav .caret{display:inline-block;width:5px;height:5px;border-right:1px solid #333;border-bottom:1px solid #333;transform:rotate(45deg);margin-left:5px;position:relative;top:-2px}

/* hero + mega menu */
.hero{top:84px;height:449px;background:linear-gradient(180deg,var(--blue-light),var(--blue-dark))}
.mega{left:130px;top:3px;width:940px;height:370px;background:#fff}
.mega-col{position:absolute;top:40px}
.mega-col h4{font-family:"Montserrat",sans-serif;font-weight:500;font-size:15px;color:#222;margin-bottom:12px}
.mega-col li{list-style:none;font-size:10.5px;line-height:23.3px;color:#333}
.mega-col li.sub{color:var(--accent-red);font-size:9.5px;line-height:18px;padding-left:8px;position:relative}
.mega-col li.sub::before{content:"";position:absolute;left:0;top:7px;width:4px;height:4px;border-radius:50%;background:var(--accent-red)}
.mega-divider{position:absolute;top:50px;width:1px;height:272px;background:var(--line)}

/* team */
.team{top:533px;height:507px;background:radial-gradient(ellipse at 60% 40%,var(--team-mid),var(--team-dark) 75%)}
.team h2{position:absolute;top:68px;width:100%;text-align:center;font-family:"Raleway",sans-serif;font-weight:800;font-size:33px;color:#fff;letter-spacing:.5px}
.team .name{position:absolute;top:136px;width:100%;text-align:center;font-family:"Raleway",sans-serif;font-size:24px;color:#fff}
.team .role{position:absolute;top:167px;width:100%;text-align:center;font-size:11px;color:#e8efe8}
.chev{position:absolute;width:10px;height:10px;border-left:2px solid #fff;border-bottom:2px solid #fff}
.portrait{position:absolute}
.portrait.main{left:524px;top:200px;width:152px;height:233px;background:linear-gradient(180deg,#cfd6d8,#8a8f93)}
.portrait.side{top:227px;width:152px;height:206px;background:linear-gradient(180deg,#4d7a4b,#36613a);opacity:.9}

/* services */
.services{top:1040px;height:1110px;background:#fff}
.services h2{position:absolute;top:68px;width:100%;text-align:center;font-family:"Raleway",sans-serif;font-weight:800;font-size:33px;color:#111}
.svc{position:absolute;width:290px;transform:translateX(-50%);text-align:center}
.svc .ico{width:76px;height:76px;border-radius:50%;border:1.5px solid #2a9fd0;margin:0 auto;display:flex;align-items:center;justify-content:center}
.svc h3{margin-top:14px;font-family:"Raleway",sans-serif;font-weight:500;font-size:17px;color:#222}
.svc p{margin:12px auto 0;width:272px;font-size:10px;line-height:15.5px;color:#444}
.svc a{display:inline-block;margin-top:11px;font-size:9.5px;color:var(--accent-red);text-decoration:underline}

/* testimonials */
.testimonials{top:2150px;height:510px;background:linear-gradient(180deg,#679a5d,#578a51)}
.testimonials .kicker{position:absolute;top:66px;width:100%;text-align:center;font-family:"Raleway",sans-serif;font-size:15px;color:#fff}
.testimonials h2{position:absolute;top:88px;width:100%;text-align:center;font-family:"Raleway",sans-serif;font-weight:800;font-size:32px;color:#fff}
.card{position:absolute;top:155px;width:299px;height:288px;background:#fff;border-radius:3px}
.card .avatar{position:absolute;left:22px;top:20px;width:56px;height:56px;border-radius:50%;background:linear-gradient(135deg,#b9a38d,#6b5a4f)}
.card .stars{position:absolute;left:80px;top:20px;font-size:13px;color:var(--star);letter-spacing:2px}
.card .who{position:absolute;left:80px;top:53px;font-family:"Raleway",sans-serif;font-size:17px;font-weight:500}
.card .quote{position:absolute;left:23px;top:101px;width:258px;font-size:10.5px;line-height:16.5px;color:#444}
.card .quote span{color:var(--accent-red)}
.card .date{position:absolute;left:23px;top:203px;font-size:10px;color:#666}
.card .rule{position:absolute;left:23px;right:18px;top:233px;height:1px;background:var(--line)}
.card .source{position:absolute;left:23px;top:253px;font-size:10px;color:#444}
.card .sites{position:absolute;right:18px;top:250px;font-size:13px;font-weight:600;color:#555;display:flex;gap:16px}
.arrow-box{position:absolute;top:284px;width:30px;height:30px;border:1px solid rgba(255,255,255,.7)}
.arrow-box i{position:absolute;top:11px;width:8px;height:8px;border-left:1.5px solid #fff;border-bottom:1.5px solid #fff}

/* difference */
.difference{top:2660px;height:612px;background:var(--soft-bg)}
.difference .kicker{position:absolute;left:130px;top:72px;font-family:"Raleway",sans-serif;font-size:16px;color:#222}
.difference h2{position:absolute;left:130px;top:96px;font-family:"Raleway",sans-serif;font-weight:800;font-size:33px;color:#1b1b1b}
.diff-body{position:absolute;left:130px;top:168px;width:540px;font-size:12.4px;line-height:19.5px;color:#333}
.diff-body p{margin-bottom:14px}
.diff-body p.tight{margin-bottom:0}
.diff-cta{position:absolute;left:130px;top:515px;font-family:"Raleway",sans-serif;font-size:20px;color:#222}
.diff-cta span{color:var(--accent-red);font-weight:500}
.diff-photo{position:absolute;left:690px;top:76px;width:380px;height:458px;background:linear-gradient(160deg,#dfe7ea,#b8d7dd 60%,#9fcfcc)}

/* CTA */
.commit{top:3272px;height:308px;background:linear-gradient(180deg,#1aa0dc,#0e87c8)}
.commit .kicker{position:absolute;top:70px;width:100%;text-align:center;font-family:"Raleway",sans-serif;font-size:16px;color:#fff}
.commit h2{position:absolute;top:93px;width:100%;text-align:center;font-family:"Raleway",sans-serif;font-weight:800;font-size:33px;color:#fff}
.commit .offer{position:absolute;top:148px;width:100%;text-align:center;font-family:"Raleway",sans-serif;font-weight:500;font-size:20px;color:#fff}
.btn-book{position:absolute;left:521px;top:202px;width:156px;height:30px;border-radius:15px;background:var(--accent-red);color:#fff;font-size:10px;font-weight:600;display:flex;align-items:center;justify-content:center}

/* footer */
.footer{top:3580px;height:357px;background:var(--footer-bg);color:#bbb}
.footer h4{position:absolute;top:39px;font-size:12px;font-weight:500;color:var(--footer-head);letter-spacing:.3px}
.f-info{position:absolute;left:130px;top:72px;font-size:10.5px;line-height:17px;color:#bbb}
.f-info .row{display:flex;gap:8px;margin-bottom:16px}
.f-info svg{flex:none;margin-top:3px}
.hours{margin-top:4px}
.map{position:absolute;left:450px;top:72px;width:300px;height:159px;background:linear-gradient(135deg,#e9ece6,#d6ddd2)}
.other{position:absolute;left:450px;top:276px;font-size:10.5px;line-height:16px;color:#ccc}
.other .links{color:#8ab1cf}
.review-list{position:absolute;left:978px;top:73px}
.review-list .item{display:flex;align-items:center;gap:12px;height:34px;margin-bottom:13px;font-size:10.5px;color:#bbb}
.review-list .circ{width:34px;height:34px;border-radius:50%;background:#fff}
.footer-bar{top:3937px;height:55px;background:var(--footer-bar);color:#ccc;font-size:10.5px;display:flex;align-items:center;justify-content:center}
.footer-bar .site{color:#6cb1d9}
</style>
</head>
<body>

<svg width="0" height="0" style="position:absolute">
  <symbol id="tooth" viewBox="0 0 40 40">
    <path d="M20 9c-3-3-9-3-11 1s0 9 1.5 12c1.5 3 1.5 10 4 10s2-7 5.5-7 3 7 5.5 7 2.5-7 4-10 3.5-8 1.5-12-8-4-11-1z" fill="none" stroke="#2a9fd0" stroke-width="1.6" stroke-linejoin="round"/>
  </symbol>
</svg>

<!-- Header -->
<header class="section site-header">
  <div class="abs brand"><span>Bright Harbor</span><span class="brand-dot"></span></div>
  <div class="abs topline">Maple Grove: <b>(555) 014-2290</b></div>
  <div class="abs btn-pill btn-schedule">SCHEDULE ONLINE</div>
  <div class="abs btn-pill btn-emergency">EMERGENCY</div>
  <nav class="nav">
    <a class="active" style="left:406px">Home</a>
    <a style="left:476px">About Us</a>
    <a style="left:553px">Service<span class="caret"></span></a>
    <a style="left:626px">Financing<span class="caret"></span></a>
    <a style="left:708px">Testimonials</a>
    <a style="left:814px">New Patient Visit</a>
    <a style="left:910px">Specials</a>
    <a style="left:989px">Contact Us</a>
    <a style="left:1060px">Blog</a>
  </nav>
  <svg class="abs" style="left:396px;top:66px" width="20" height="8"><path d="M1 1q9 8 18 0" fill="none" stroke="#e0262c" stroke-width="1.3"/></svg>
</header>

<!-- Hero with services menu -->
<section class="section hero" role="img" aria-label="Blue hero banner with a tooth illustration">
  <div class="abs mega">
    <div class="mega-col" style="left:17px">
      <h4>Implants</h4>
      <ul>
        <li>Dental Implants</li>
        <li class="sub">Full Mouth Dental Implants</li>
        <li class="sub">Mini Dental Implants</li>
        <li class="sub">Permanent Dentures</li>
        <li class="sub">Same Day Dental Implants</li>
        <li class="sub">FAQ</li>
        <li>Denture Stabilization</li>
        <li>Bone Grafting/Sinus Lift</li>
      </ul>
    </div>
    <div class="mega-divider" style="left:211px"></div>
    <div class="mega-col" style="left:275px">
      <h4>Cosmetic Dentistry</h4>
      <ul>
        <li>Dental Crowns</li>
        <li>Dental Veneers</li>
        <li>Dentures</li>
        <li>Complete Dentures</li>
        <li>Partial Dentures</li>
        <li class="sub">Teeth Whitening/GlowLite!</li>
        <li class="sub">Gum Reconstruction</li>
        <li>Dental Bonding</li>
        <li>Tooth Color Restoration</li>
        <li>Cosmetic Smile</li>
        <li>Assessment</li>
      </ul>
    </div>
    <div class="mega-divider" style="left:475px"></div>
    <div class="mega-col" style="left:538px">
      <h4>General</h4>
      <ul>
        <li>Tooth Extraction</li>
        <li>Wisdom Tooth Extractions</li>
        <li>Endodontics</li>
        <li class="sub">Root Canal</li>
        <li>Dental Bridges</li>
        <li>Sedation Dentistry</li>
        <li>Dental Emergency</li>
        <li>Bruxism/Teeth Grinding</li>
        <li>Children's Dentistry</li>
        <li>Metal Free Dentistry</li>
        <li>Laser Dentistry</li>
        <li>Gum Disease</li>
      </ul>
    </div>
    <div class="mega-divider" style="left:727px"></div>
    <div class="mega-col" style="left:791px">
      <h4>Orthodontics</h4>
      <ul><li>ClearAlign® for Adults</li></ul>
    </div>
  </div>
</section>

<!-- Team -->
<section class="section team">
  <h2>MEET OUR TEAM</h2>
  <div class="name">Dr. Nikhil Arora</div>
  <div class="role">General Dentist (DDS)</div>
  <span class="chev" style="left:462px;top:156px;transform:rotate(45deg)"></span>
  <span class="chev" style="left:730px;top:156px;transform:rotate(-135deg)"></span>
  <div class="portrait side" style="left:302px" role="img" aria-label="Portrait of a team dentist, dimmed"></div>
  <div class="portrait main" role="img" aria-label="Portrait of the featured dentist in a white coat"></div>
  <div class="portrait side" style="left:742px" role="img" aria-label="Portrait of a team dentist, dimmed"></div>
</section>

<!-- Services -->
<section class="section services">
  <h2>OUR SERVICES</h2>

  <div class="svc" style="left:279px;top:134px"><div class="ico"><svg width="42" height="42"><use href="#tooth"/></svg></div><h3>Dental Implants</h3><p>Lost teeth? Live your life better and healthier by having a permanent teeth restoration at My Bright Harbor Dental Office.</p><a>READ MORE</a></div>
  <div class="svc" style="left:600px;top:134px"><div class="ico"><svg width="42" height="42"><use href="#tooth"/></svg></div><h3>Cosmetic Dentistry</h3><p>Dental bridges are an important part of your oral health, created to address a gap in your teeth from having a permanent tooth removed.</p><a>READ MORE</a></div>
  <div class="svc" style="left:919px;top:134px"><div class="ico"><svg width="42" height="42"><use href="#tooth"/></svg></div><h3>Braces</h3><p>Dental bridges are an important part of your oral health, created to address a gap in your teeth from having a permanent tooth removed.</p><a>READ MORE</a></div>

  <div class="svc" style="left:279px;top:368px"><div class="ico"><svg width="42" height="42"><use href="#tooth"/></svg></div><h3>Crowns</h3><p>A dental crown is a tooth-shaped cap that is placed over a damaged or misshapen tooth to improve its structural integrity or appearance.</p><a>READ MORE</a></div>
  <div class="svc" style="left:600px;top:368px"><div class="ico"><svg width="42" height="42"><use href="#tooth"/></svg></div><h3>Bridge</h3><p>Dental bridges are an important part of your oral health, created to address a gap in your teeth from having a permanent tooth removed.</p><a>READ MORE</a></div>
  <div class="svc" style="left:919px;top:368px"><div class="ico"><svg width="42" height="42"><use href="#tooth"/></svg></div><h3>Extractions</h3><p>Tooth extraction is a dental procedure where a tooth is removed from its bone socket. When a tooth is severely damaged</p><a>READ MORE</a></div>

  <div class="svc" style="left:279px;top:602px"><div class="ico"><svg width="42" height="42"><use href="#tooth"/></svg></div><h3>Gum Disease</h3><p>Gum disease, also known as periodontal disease, is an infection of the tissues supporting and around your teeth.</p><a>READ MORE</a></div>
  <div class="svc" style="left:600px;top:602px"><div class="ico"><svg width="42" height="42"><use href="#tooth"/></svg></div><h3>Root Canal</h3><p>You must have heard of the treatment called root canal, but do you know what it is really for? Why this procedure is needed</p><a>READ MORE</a></div>
  <div class="svc" style="left:919px;top:602px"><div class="ico"><svg width="42" height="42"><use href="#tooth"/></svg></div><h3>Dentures</h3><p>If you are out of budget and still want to restore your confident smile, a denture treatment is the right option for you.</p><a>READ MORE</a></div>

  <div class="svc" style="left:279px;top:836px"><div class="ico"><svg width="42" height="42"><use href="#tooth"/></svg></div><h3>Emergency Dentistry</h3><p>If you are out of budget and still want to restore your confident smile, a denture treatment is the right option for you.</p><a>READ MORE</a></div>
  <div class="svc" style="left:600px;top:836px"><div class="ico"><svg width="42" height="42"><use href="#tooth"/></svg></div><h3>Veneers</h3><p>If you are out of budget and still want to restore your confident smile, a denture treatment is the right option for you.</p><a>READ MORE</a></div>
  <div class="svc" style="left:919px;top:836px"><div class="ico"><svg width="42" height="42"><use href="#tooth"/></svg></div><h3>ClearAlign Aligners</h3><p>ClearAlign® are custom, removable clear plastic aligners that can be worn in both the lower and upper jaws to straighten teeth.</p><a>READ MORE</a></div>
</section>

<!-- Testimonials -->
<section class="section testimonials">
  <div class="kicker">WHAT OUR</div>
  <h2>PATIENTS SAY ABOUT US</h2>
  <div class="arrow-box" style="left:50px"><i style="left:12px;transform:rotate(45deg)"></i></div>
  <div class="arrow-box" style="left:1120px"><i style="left:8px;transform:rotate(-135deg)"></i></div>

  <article class="card" style="left:130px">
    <div class="avatar" role="img" aria-label="Patient photo"></div>
    <div class="stars">★★★★★</div>
    <div class="who">Tara M.</div>
    <p class="quote">I have never been an easy patient. Everything terrifies me. I have had SUCH a great experience with Bright Harbor... Marla in particular has especially been kind and helpful. From the very first time I walked into...<span>More</span></p>
    <div class="date">08 October, 2021</div>
    <div class="rule"></div>
    <div class="source">Source:</div>
    <div class="sites"><span>Searchly</span><span>Rateit</span></div>
  </article>
  <article class="card" style="left:450px">
    <div class="avatar" role="img" aria-label="Patient photo"></div>
    <div class="stars">★★★★★</div>
    <div class="who">Renee D.</div>
    <p class="quote">I am so happy I found Bright Harbor in Maple Grove. This is a long over due review since I have been seeing them for almost two years. They are always so friendly, understanding and empathetic when they have to deliver n...<span>More</span></p>
    <div class="date">05 October, 2021</div>
    <div class="rule"></div>
    <div class="source">Source:</div>
    <div class="sites"><span>Searchly</span><span>Rateit</span></div>
  </article>
  <article class="card" style="left:770px">
    <div class="avatar" role="img" aria-label="Patient photo"></div>
    <div class="stars">★★★★★</div>
    <div class="who">Alicia S.</div>
    <p class="quote">Starting coming to this dentist and I wish I could have found them sooner. Everyone here is super nice and helpful. They have everything you need here very clean and modern with upgraded equipment. I've been recommended...<span>More</span></p>
    <div class="date">28 September, 2021</div>
    <div class="rule"></div>
    <div class="source">Source:</div>
    <div class="sites"><span>Searchly</span><span>Rateit</span></div>
  </article>
</section>

<!-- Difference -->
<section class="section difference">
  <div class="kicker">EXPERIENCE THE</div>
  <h2>BRIGHT HARBOR DIFFERENCE</h2>
  <div class="diff-body">
    <p>Your smile is our #1 priority. At Bright Harbor, we provide affordable and expert dental solutions. Whether you are looking for a family dentist or have any emergency such as needing a root canal in Maple Grove, we are here for you! We want to keep your teeth healthy inside and out. We don't just clean teeth and send you on your way, we want to get to know you.</p>
    <p class="tight">We accept most HMO and PPO insurances. We offer various financing options through CarePay, LendWell and In-House Plans.</p>
    <p>To constantly strive to achieve the highest level of skills and modern techniques and equipment so we can provide our patients with the best that Dentistry has to offer at our dental office in Maple Grove, Harbor County, CA.</p>
    <p>We provide patients with the best experience you can find in all of the Coast Region. We provide a comfortable and friendly atmosphere to shatter any fears you may have. We supply you with all the information on your dental health options so you can feel comfortable in the choices you make, whether it's a routine check-up or dental implants in Maple Grove.</p>
  </div>
  <div class="diff-cta">We are available for <span>Emergency and Walk-ins.</span></div>
  <div class="diff-photo" role="img" aria-label="Smiling patient in a dental chair giving a thumbs up"></div>
</section>

<!-- Commitment CTA -->
<section class="section commit">
  <div class="kicker">COMMITTED TO</div>
  <h2>EXCELLENCE IN ORAL HEALTH CARE</h2>
  <div class="offer">Free Exam and X-Rays for New Patients</div>
  <div class="btn-book">BOOK AN APPOINTMENT</div>
</section>

<!-- Footer -->
<footer class="section footer">
  <h4 style="left:130px">BRIGHT HARBOR</h4>
  <h4 style="left:450px">MAP &amp; DIRECTIONS</h4>
  <h4 style="left:978px">REVIEW US</h4>
  <div class="f-info">
    <div class="row"><svg width="9" height="12"><path d="M4.5 0a4.5 4.5 0 0 1 4.5 4.5C9 8 4.5 12 4.5 12S0 8 0 4.5A4.5 4.5 0 0 1 4.5 0z" fill="#7cb24f"/><circle cx="4.5" cy="4.5" r="1.6" fill="#232323"/></svg><div>48 Linden Row Ave., Suite A<br>Maple Grove, CA 90000</div></div>
    <div class="row"><svg width="10" height="10"><path d="M2 0l2 2.5-1 1.5q1.5 2.5 3 3l1.5-1L10 8l-1.5 2Q3 9.5 0 1.5z" fill="#7cb24f"/></svg><div>Call Us: (555) 014-2290</div></div>
    <div class="row"><svg width="10" height="8"><rect width="10" height="8" fill="#7cb24f"/><path d="M0 0l5 4 5-4" fill="none" stroke="#232323"/></svg><div>hello@mybrightharbor.example</div></div>
    <div class="hours">Office Hours:<br>Monday 10AM–7PM<br>Tuesday 10AM–7PM<br>Wednesday 9AM–6PM<br>Thursday 9AM–6PM<br>Friday 9AM–5PM<br>Saturday 9AM–1PM</div>
  </div>
  <div class="map" role="img" aria-label="Street map showing the office location"></div>
  <div class="other">Other Locations:<br><span class="links">Ridge Dental | Lakeview Dental | Bayside Dental |<br>Cedar Dental | Harborline Dental</span></div>
  <div class="review-list">
    <div class="item"><span class="circ"></span>Searchly+</div>
    <div class="item"><span class="circ"></span>Rateit</div>
    <div class="item"><span class="circ"></span>Friendbook</div>
    <div class="item"><span class="circ"></span>Chirper</div>
  </div>
</footer>
<div class="section footer-bar">All rights reserved.&nbsp;<span class="site">MyBrightHarbor.example</span>&nbsp;| Disclaimer &amp; Terms | Privacy Policy | Sitemap</div>

</body>
</html>
```